ELsewhen website redesign to provide information about experiential workshops, film work and other

We need a redesign of our website elsewhen.org. We conduct experiential workshops of discovery and transformation for individuals and organizations. We need the website to reflect the full extent of ELsewhen programs, and be an information hub for ELsewhen workshops and communities as they develop.

The attached documents contain information about the organization - it's brandbook, copy for web pages, a website layout and a couple of images.

The site is for individuals and companies looking to promote and be change to make a difference. It should be warm, welcoming, and create excitement around the concepts and the ability to discover a new way of being in the world. We are about creating communities around the globe who will embody play, freedom, curiosity and expanded possibilities. We are creating a space for this to happen, both physically (workshops) and online.

We will be on either a SquareSpace, but mos tlikely a Weebly plaform.

Please look at the current site at www.elsewhen.org

Target Market(s)

Initially, are target market will be baby boomers, but will expand to include millennials and students.

Coding

Coded - Design and coding required

Number of Pages Required

5+ page

Requirements
Must have
• The colors, logo and fonts from the brand book.
Nice to have
• Complimentary use of brand colors to create an attractive presentation and energy

```html
<!DOCTYPE html>
<html lang="en">
<head>
<meta charset="utf-8">
<title>ELsewhen — Home</title>
<link rel="stylesheet" href="https://fonts.googleapis.com/css2?family=Jost:wght@400;500;700&family=Open+Sans:wght@400;600;700&display=swap">
<style>
:root{
  --orange:#f26a35;
  --orange-soft:#f7a351;
  --amber:#eea53a;
  --green:#6db56d;
  --gold:#f0a73b;
  --red:#e2541c;
  --ink:#1f1f1f;
  --text:#555;
  --symbol-fill:#f6e3d8;
  --white:#fff;
}
*{box-sizing:border-box;margin:0;padding:0}
html,body{width:1200px;height:4091px;overflow:hidden}
body{position:relative;font-family:"Open Sans",sans-serif;color:var(--ink);background:var(--white)}
.section{position:absolute;left:0;width:1200px}
.abs{position:absolute}
.heading{font-family:"Jost",sans-serif;font-weight:400}

/* header */
.site-header{top:0;height:104px;background:var(--white)}
.brand{left:95px;top:30px;display:flex;align-items:center;gap:12px;font-family:"Jost",sans-serif;font-weight:700;font-size:38px;letter-spacing:2px;color:var(--ink)}
.brand-mark{width:34px;height:34px;background:var(--orange)}
.header-btn{top:33px;height:41px;width:163px;border-radius:8px;color:var(--white);font-size:16px;font-weight:600;display:flex;align-items:center;justify-content:center}
.btn-email{left:764px;background:var(--green)}
.btn-login{left:944px;background:var(--gold)}

.main-nav{top:104px;height:65px;background:var(--orange)}
.main-nav ul{list-style:none;display:flex;height:65px;padding-left:90px}
.main-nav li{display:flex;align-items:center;padding:0 11px;color:var(--white);font-size:14px;text-transform:uppercase;margin-right:14px}
.main-nav li.active{background:var(--orange-soft)}

/* hero */
.hero{top:169px;height:521px;background:radial-gradient(ellipse at 50% 80%,#5a5f52 0%,#2c3a2a 35%,#142016 75%,#0b120c 100%)}
.hero h1{position:absolute;top:200px;width:100%;text-align:center;color:var(--white);font-family:"Jost",sans-serif;font-weight:400;font-size:46px;line-height:64px}
.hero h1 span{display:block;font-size:40px}

/* about */
.about{top:690px;height:537px}
.frame-line{left:101px;top:90px;width:417px;height:324px;border:2px solid #d6d6d6}
.frame-fill{left:117px;top:106px;width:407px;height:328px;background:var(--orange)}
.about-photo{left:134px;top:123px;width:403px;height:327px;background:linear-gradient(135deg,#6a4a2c,#b07a4a 45%,#7b5b3b 80%,#3f2e1f)}
.about h2{left:567px;top:155px;font-size:46px;color:var(--ink)}
.benefits{left:570px;top:220px;list-style:none}
.benefits li{display:flex;align-items:center;gap:14px;height:40px;font-size:19px;color:var(--text)}

/* vision */
.vision{top:1227px;height:499px;background:linear-gradient(100deg,var(--red) 0%,#e85d22 40%,#c93e14 70%,#8f2410 100%)}
.vision h2{left:90px;top:75px;font-size:42px;color:var(--white)}
.vision-copy{left:90px;top:144px;width:560px;color:var(--white);font-size:17px;line-height:32px}
.vision-copy p+p{margin-top:18px}

/* what we do */
.what{top:1726px;height:720px}
.what h2{top:95px;width:100%;text-align:center;font-size:42px}
.what-intro{left:150px;top:170px;width:900px;text-align:center;font-size:15px;line-height:35px;color:var(--text)}
.what h3{top:298px;width:100%;text-align:center;font-size:28px;line-height:38px;color:var(--ink)}
.movement{top:423px;width:180px;margin-left:-90px;text-align:center}
.movement-symbol{display:block;width:128px;height:128px;margin:0 auto;border-radius:50%;border:3px solid var(--orange);background:var(--symbol-fill)}
.movement p{margin-top:14px;font-size:18px;line-height:24px;color:var(--ink)}

/* program */
.program{top:2446px;height:527px;background:linear-gradient(120deg,#f0ae48,var(--amber) 50%,#e3962a)}
.program-box{left:104px;top:104px;width:551px;height:354px;border:2px solid var(--white)}
.program-photo{left:657px;top:120px;width:437px;height:306px;background:linear-gradient(160deg,#2f3d2f,#5b6356 50%,#2a2a2a)}
.program h2{left:153px;top:160px;font-size:36px;color:var(--white)}
.program-copy{left:153px;top:217px;width:480px;font-size:13.5px;line-height:29px;color:var(--white)}
.btn-read{left:153px;top:382px;width:112px;height:30px;border-radius:15px;background:var(--orange);color:var(--white);font-size:14px;display:flex;align-items:center;justify-content:center}

/* community */
.community{top:2973px;height:695px}
.community h2{top:100px;width:100%;text-align:center;font-size:40px}
.community-sub{top:168px;width:100%;text-align:center;font-size:16px;line-height:30px;color:var(--text)}
.form-card{left:196px;top:261px;width:808px;height:319px;background:var(--white);box-shadow:0 2px 14px rgba(0,0,0,.2)}
.field{height:55px;border:2px solid #d3d3d3;box-shadow:inset 0 1px 3px rgba(0,0,0,.12);font-size:14px;color:#444;display:flex;align-items:center;padding-left:18px}
.btn-submit{left:344px;top:262px;width:120px;height:35px;border-radius:6px;background:var(--orange);color:var(--white);font-size:17px;display:flex;align-items:center;justify-content:center}

/* footer */
.footer-rule{top:3668px;height:19px;background:var(--orange)}
.site-footer{top:3687px;height:404px;background:linear-gradient(180deg,#1c1c1c,#141414)}
.site-footer h4{font-family:"Jost",sans-serif;font-weight:400;font-size:21px;color:var(--white);top:82px}
.contact-item{left:95px;display:flex;gap:12px;color:var(--white)}
.contact-item b{display:block;font-size:15px;font-weight:600;text-transform:uppercase}
.contact-item span{display:block;font-size:13px;color:#d8d8d8}
.footer-links{list-style:none;top:132px}
.footer-links li{height:33px;font-size:15px;color:var(--white)}
.news-input{left:796px;top:131px;width:295px;height:46px;border:1px solid #8a8a8a;color:var(--white);font-size:14px;display:flex;align-items:center;padding-left:16px}
.btn-subscribe{left:796px;top:186px;width:295px;height:46px;background:var(--orange);color:var(--white);font-size:17px;display:flex;align-items:center;justify-content:center}
.footer-divider{left:95px;top:311px;width:1010px;height:1px;background:#3c3c3c}
.copyright{top:348px;width:100%;text-align:center;font-size:13px;color:#bdbdbd}
</style>
</head>
<body>

<header class="section site-header">
  <div class="abs brand"><span class="brand-mark"></span>ELSEWHEN</div>
  <div class="abs header-btn btn-email">Email Capture</div>
  <div class="abs header-btn btn-login">Member Login</div>
</header>

<nav class="section main-nav">
  <ul>
    <li class="active">Home</li>
    <li>About Us</li>
    <li>Workshops</li>
    <li>ELsewhen Projects</li>
    <li>Films</li>
    <li>Store &amp; Resources</li>
    <li>Community</li>
    <li>Contact Us</li>
  </ul>
</nav>

<section class="section hero" role="img" aria-label="Photograph of a wooden suspension bridge leading into a dark green forest">
  <h1>What World Do We Want to Live In?<span>What Kind of Life Do You Want to Create?</span></h1>
</section>

<section class="section about">
  <div class="abs frame-line"></div>
  <div class="abs frame-fill"></div>
  <div class="abs about-photo" role="img" aria-label="Photograph of workshop participants sitting together on a patterned rug"></div>
  <h2 class="abs heading">ELsewhen:</h2>
  <ul class="abs benefits">
    <li><svg width="18" height="18" viewBox="0 0 18 18"><circle cx="9" cy="9" r="9" fill="#f26a35"/><path d="M10.5 5 6.5 9l4 4" stroke="#fff" stroke-width="2" fill="none"/></svg>Moves Energy</li>
    <li><svg width="18" height="18" viewBox="0 0 18 18"><circle cx="9" cy="9" r="9" fill="#f26a35"/><path d="M10.5 5 6.5 9l4 4" stroke="#fff" stroke-width="2" fill="none"/></svg>Creates Opportunities for Connecting</li>
    <li><svg width="18" height="18" viewBox="0 0 18 18"><circle cx="9" cy="9" r="9" fill="#f26a35"/><path d="M10.5 5 6.5 9l4 4" stroke="#fff" stroke-width="2" fill="none"/></svg>Supports Conscious Evolution</li>
    <li><svg width="18" height="18" viewBox="0 0 18 18"><circle cx="9" cy="9" r="9" fill="#f26a35"/><path d="M10.5 5 6.5 9l4 4" stroke="#fff" stroke-width="2" fill="none"/></svg>Deepens Experience of Life</li>
    <li><svg width="18" height="18" viewBox="0 0 18 18"><circle cx="9" cy="9" r="9" fill="#f26a35"/><path d="M10.5 5 6.5 9l4 4" stroke="#fff" stroke-width="2" fill="none"/></svg>Provides Opportunities for Collaboration and Creation</li>
  </ul>
</section>

<section class="section vision" role="img" aria-label="Orange-toned photograph of people dancing in colourful costumes">
  <h2 class="abs heading">Vision</h2>
  <div class="abs vision-copy">
    <p>We envision a world in which all people and communities can challenge and break free from stories that no longer serve us. We believe that solutions to contemporary challenges will emerge from a place of curiosity, love and connection.</p>
    <p>Through inspiration, conscious reflection, and collaboration, we take responsibility for the world we are manifesting, and we can discover and create new possibilities for the lives and the society we desire to build.</p>
  </div>
</section>

<section class="section what">
  <h2 class="abs heading">What We Do</h2>
  <p class="abs what-intro">ELsewhen Life is a workshop designed to re-engage you with life. Through interactive exercises and personal exploration, you are taken on a journey that ultimately leaves you experiencing life as a Creator. You will learn to see beliefs and patterns that hold you back in work and relationships as well as a path to transforming the story of your life.</p>
  <h3 class="abs heading">ELsewhen Life is a 2-3 day workshop<br>experienced in 5 movements:</h3>

  <div class="abs movement" style="left:224px">
    <div class="movement-symbol" role="img" aria-label="Symbol for the Curiosity movement"></div>
    <p>Curiosity</p>
  </div>
  <div class="abs movement" style="left:412px">
    <div class="movement-symbol" role="img" aria-label="Symbol for the Awareness movement"></div>
    <p>Awareness</p>
  </div>
  <div class="abs movement" style="left:600px">
    <div class="movement-symbol" role="img" aria-label="Symbol for the Owning Your Creation movement"></div>
    <p>Owning Your<br>Creation</p>
  </div>
  <div class="abs movement" style="left:785px">
    <div class="movement-symbol" role="img" aria-label="Symbol for the Reimagining movement"></div>
    <p>Reimagining</p>
  </div>
  <div class="abs movement" style="left:971px">
    <div class="movement-symbol" role="img" aria-label="Symbol for the Manifesting movement"></div>
    <p>Manifesting</p>
  </div>
</section>

<section class="section program" role="img" aria-label="Amber-toned photograph of framed pictures on a wall">
  <div class="abs program-box"></div>
  <div class="abs program-photo" role="img" aria-label="Photograph of a group seated in a circle during a workshop session"></div>
  <h2 class="abs heading">Unsettling the Calm</h2>
  <p class="abs program-copy">The Unsettling the Calm workshop—an extension of the documentary of the same name—is an experiential process to transform participants into disturbers of the status quo within themselves, to enhance their relationships with others, and to change the environments in which they exist—and ultimately society—for the better.</p>
  <div class="abs btn-read">Read More</div>
</section>

<section class="section community">
  <h2 class="abs heading">In Your Community</h2>
  <p class="abs community-sub">Bring ELsewhen or the Unsettling the Calm workshop to your community.<br>We wouldlove to hear from you.</p>
  <form class="abs form-card">
    <div class="abs field" style="left:33px;top:47px;width:357px">Name</div>
    <div class="abs field" style="left:409px;top:47px;width:360px">Phone</div>
    <div class="abs field" style="left:33px;top:117px;width:736px">Email id</div>
    <div class="abs field" style="left:33px;top:186px;width:736px">Message</div>
    <div class="abs btn-submit">Submit</div>
  </form>
</section>

<div class="section footer-rule"></div>
<footer class="section site-footer">
  <h4 class="abs" style="left:95px">CONTACT US</h4>
  <div class="abs contact-item" style="top:134px">
    <svg width="20" height="16" viewBox="0 0 20 16"><rect x="1" y="1" width="18" height="14" fill="none" stroke="#fff" stroke-width="1.6"/><path d="M1 2l9 7 9-7" fill="none" stroke="#fff" stroke-width="1.6"/></svg>
    <div><b>Email Address</b><span>info@elsewhen.org</span></div>
  </div>
  <div class="abs contact-item" style="top:199px">
    <svg width="20" height="20" viewBox="0 0 20 20"><path d="M5 2l3 4-2 2c1 2 3 4 5 5l2-2 4 3-2 3C9 17 3 11 2 4z" fill="none" stroke="#fff" stroke-width="1.5" stroke-linejoin="round"/></svg>
    <div><b>Phone Number</b><span>(555) 014-2290</span></div>
  </div>

  <h4 class="abs" style="left:390px">ABOUT</h4>
  <ul class="abs footer-links" style="left:390px"><li>Home</li><li>About Us</li><li>Services</li><li>Treatment</li></ul>

  <h4 class="abs" style="left:567px">RESOURCES</h4>
  <ul class="abs footer-links" style="left:567px"><li>Support</li><li>Why Us</li><li>Testimonials</li><li>FAQ</li></ul>

  <h4 class="abs" style="left:794px">NEWSLETTERS</h4>
  <div class="abs news-input">Email address</div>
  <div class="abs btn-subscribe">Subscribe Now</div>

  <div class="abs footer-divider"></div>
  <p class="abs copyright">© 2018 Company Name &nbsp;All right reserved</p>
</footer>

</body>
</html>
```